International Travel Technology R&D business needs a wordpress website

We are a start up team of initially 2 individuals but plan to grow our team quickly, we have deep experience in travel technology. Our goal is to provide next generation technology research and development on behalf of our clients who are leading players in the travel technology industry. Attached our logos.

Target Market(s)

Travel Technology companies

Industry/Entity Type

Travel Industry

Coding

Coded - Design and coding required

Font styles to use
Sans Serif

Requirements
Must have
• Make use of our logo and colour scheme in the attached. Has to have a sense of adventure/ stepping into the unknown but equally must convey a sense of professionalism , we are a safe pair of hands. Sample themes are in the attachment .
Nice to have
• We have identified a theme on skinharbor which we feel would be inspirational. We hahe attached them to help in the design as inspiration.
Should not have
• images of airplanes , hotels etc, we want to project a future image.

```html
<!DOCTYPE html>
<html lang="en">
<head>
<meta charset="utf-8">
<title>Voyage Forge Labs</title>
<link rel="stylesheet" href="https://fonts.googleapis.com/css2?family=Open+Sans:wght@400;600&family=Roboto+Condensed:wght@300;400&display=swap">
<style>
:root{
  --blue:#6b9fd9;
  --blue-dark:#5a8dc8;
  --green:#6caf45;
  --green-deep:#5f9e3b;
  --ink:#3d3d3d;
  --text:#666;
  --light:#f1f1f1;
  --footer:#262626;
  --white:#fff;
}
*{margin:0;padding:0;box-sizing:border-box}
html,body{width:1200px;height:2808px;overflow:hidden}
body{position:relative;background:var(--white);font-family:"Open Sans",sans-serif;color:var(--text);font-size:12px;line-height:1.6}
.abs{position:absolute}
h1,h2,h3,h4{font-family:"Roboto Condensed",sans-serif;font-weight:400}

/* header */
.topbar{left:618px;top:0;width:582px;height:28px;background:var(--blue);clip-path:polygon(0 0,100% 0,100% 100%,40px 100%);color:var(--white);font-size:12px;display:flex;align-items:center;gap:40px;padding-left:84px}
.topbar span{display:flex;align-items:center;gap:8px}
.brand{left:99px;top:44px;display:flex;align-items:center;gap:10px;font-family:"Open Sans",sans-serif;font-weight:600;font-size:20px;color:var(--blue-dark);letter-spacing:.5px}
.brand i{width:14px;height:14px;border-radius:50%;background:var(--green);display:block}
.nav{left:556px;top:66px;display:flex;gap:44px;font-size:13px;color:var(--ink);text-transform:uppercase}

/* hero */
.hero{left:0;top:112px;width:1200px;height:510px;background:linear-gradient(180deg,#8a8f96 0%,#b9a48a 45%,#6f6a66 75%,#3a3a3c 100%)}
.hero-title{left:0;top:348px;width:1200px;text-align:center;color:var(--white)}
.hero-title h1{font-size:40px;letter-spacing:.5px}
.hero-title p{font-size:12px;width:380px;margin:6px auto 0}
.arrow{top:356px;width:32px;height:32px;border-radius:50%;background:rgba(0,0,0,.35)}

/* welcome */
.welcome{left:150px;top:776px;width:900px;text-align:center}
.welcome h2{font-size:36px;color:var(--ink);font-weight:300}
.welcome p{margin-top:18px;font-size:11.5px;line-height:1.7}
.welcome-mark{left:570px;top:676px;width:60px;height:60px;border-radius:50%;background:var(--blue)}

/* section headings */
.sec-head{left:0;width:1200px;display:flex;align-items:center;justify-content:center;gap:26px}
.sec-head h2{font-size:30px;line-height:1.2}
.services-head{top:1045px;color:var(--white)}
.blog-head{top:2016px;color:var(--ink)}

/* services */
.services{left:0;top:973px;width:1200px;height:539px;background:linear-gradient(180deg,var(--green) 0%,var(--green-deep) 100%)}
.card{top:1131px;width:238px;height:299px;background:var(--white);text-align:center;padding-top:22px}
.card .icon{width:103px;height:103px;border-radius:50%;background:var(--blue);margin:0 auto;display:flex;align-items:center;justify-content:center}
.card h3{font-family:"Open Sans",sans-serif;font-size:16px;color:var(--ink);margin-top:22px}
.card p{font-size:11.5px;padding:4px 22px 0;line-height:1.55}
.btn{display:inline-block;background:var(--blue);color:var(--white);font-size:11px;padding:6px 14px;margin-top:14px}

/* feature */
.screen{left:172px;top:1591px;width:352px;height:290px;background:linear-gradient(180deg,#2b2b2b 0%,#2b2b2b 70%,#d9d9d9 70%,#bfbfbf 100%);border-radius:8px}
.feature{left:562px;top:1592px;width:480px}
.feature h2{font-size:34px;color:var(--ink);font-weight:300}
.feature p{font-size:11.5px;margin-top:12px;line-height:1.65}
.feature .lead{font-size:14px;margin-top:16px}
.feature ul{list-style:none;margin-top:12px}
.feature li{display:flex;align-items:center;gap:12px;font-size:12.5px;height:30px}

/* blog */
.blog{left:0;top:1966px;width:1200px;height:496px;background:var(--light)}
.post{top:2100px;width:313px}
.post .photo{height:193px;position:relative}
.post .date{position:absolute;left:0;bottom:0;background:var(--white);color:var(--green);font-style:italic;font-size:15px;line-height:1.25;padding:8px 14px 4px;clip-path:polygon(0 0,70% 0,100% 30%,100% 100%,0 100%)}
.post h4{font-family:"Open Sans",sans-serif;font-size:15px;color:var(--ink);margin-top:18px}
.post p{font-size:11px;margin-top:6px;line-height:1.6}

/* footer */
.footer{left:0;top:2462px;width:1200px;height:294px;background:var(--footer)}
.foot-title{font-family:"Open Sans",sans-serif;font-size:16px;color:var(--white);font-weight:400;line-height:1.3}
.foot-brand{left:99px;top:2596px;font-weight:600;font-size:22px;color:var(--white);letter-spacing:1px}
.contact{left:363px;top:2506px;width:300px}
.contact .row{display:flex;gap:18px;margin-top:20px;font-size:12.5px;color:#eee;line-height:1.6}
.news{left:680px;top:2506px;width:260px}
.news p{font-size:11px;margin-top:14px;color:#eee}
.news .field{width:242px;height:40px;background:var(--white);color:#888;font-size:11px;padding:12px;margin-top:14px}
.news .actions{display:flex;align-items:center;gap:10px;margin-top:16px}
.news .sub{background:var(--blue);color:var(--white);font-size:11px;padding:11px 18px}
.news .dot{width:24px;height:24px;border-radius:50%;background:var(--white)}
.links{left:996px;top:2506px}
.links ul{list-style:none;margin-top:14px;font-size:12px;color:var(--white);line-height:24px}
.bottom{left:0;top:2756px;width:1200px;height:52px;background:var(--blue);color:var(--white);font-size:12px;text-align:center;line-height:52px}
</style>
</head>
<body>

<header>
  <div class="abs topbar">
    <span><svg width="12" height="12" viewBox="0 0 24 24"><path fill="#fff" d="M6.6 10.8a15 15 0 0 0 6.6 6.6l2.2-2.2c.3-.3.7-.4 1-.2 1.1.4 2.3.6 3.6.6.6 0 1 .4 1 1V20c0 .6-.4 1-1 1A17 17 0 0 1 3 4c0-.6.4-1 1-1h3.5c.6 0 1 .4 1 1 0 1.3.2 2.5.6 3.6.1.3 0 .7-.2 1z"/></svg>+1 0400 555 019</span>
    <span><svg width="14" height="11" viewBox="0 0 24 18"><rect x="1" y="1" width="22" height="16" fill="none" stroke="#fff" stroke-width="2"/><path d="M1 1l11 9 11-9" fill="none" stroke="#fff" stroke-width="2"/></svg>Email: hello@voyageforge.example</span>
    <span><svg width="12" height="12" viewBox="0 0 24 24"><circle cx="10" cy="10" r="7" fill="none" stroke="#fff" stroke-width="3"/><path d="M15 15l7 7" stroke="#fff" stroke-width="3"/></svg></span>
  </div>
  <div class="abs brand"><i></i>VOYAGE FORGE LABS</div>
  <nav class="abs nav"><span>Home</span><span>About Voyage Forge</span><span>Our Services</span><span>Blog</span><span>Contact Us</span></nav>
</header>

<section>
  <div class="abs hero" role="img" aria-label="Airport terminal at sunset with a plane taking off and a traveller with luggage"></div>
  <div class="abs hero-title">
    <h1>TRAVEL TECHNOLOGY INDUSTRY</h1>
    <p>Lorem ipsum dolor sit amet, consectetur adipiscing elit, sed do eiusmod tempor incididunt ut labore</p>
  </div>
  <svg class="abs arrow" style="left:56px" viewBox="0 0 32 32"><path d="M19 10l-6 6 6 6" fill="none" stroke="#fff" stroke-width="2.5"/></svg>
  <svg class="abs arrow" style="left:1118px" viewBox="0 0 32 32"><path d="M13 10l6 6-6 6" fill="none" stroke="#fff" stroke-width="2.5"/></svg>
</section>

<section>
  <div class="abs welcome-mark"></div>
  <div class="abs welcome">
    <h2>WELCOME TO VOYAGE FORGE LABS</h2>
    <p>Nemo enim ipsam voluptatem quia voluptas sit aspernatur aut odit aut fugit, sed quia consequuntur magni dolores eos qui ratione voluptatem sequi nesciunt. Neque porro quisquam est, qui dolorem ipsum quia dolor sit amet, consectetur, adipisci velit, sed quia non numquam eius modi tempora incidunt ut labore et dolore magnam aliquam quaerat voluptatem. Ut enim ad minima veniam, quis nostrum exercitationem ullam corporis suscipit laboriosam, nisi ut aliquid ex ea commodi consequatur? Quis autem iure reprehenderit qui in ea voluptate velit esse quam nihil molestiae consequatur, vel illum qui dolorem eum fugiat quo</p>
  </div>
</section>

<section>
  <div class="abs services" role="img" aria-label="Green tinted background photo of a traveller"></div>
  <div class="abs sec-head services-head">
    <svg width="184" height="10"><polygon points="0,5 184,0 184,10" fill="#fff"/></svg>
    <h2>OUR SERVICES</h2>
    <svg width="184" height="10"><polygon points="0,0 184,5 0,10" fill="#fff"/></svg>
  </div>
  <div class="abs card" style="left:99px">
    <div class="icon"><svg width="50" height="50" viewBox="0 0 24 24"><circle cx="10" cy="10" r="6.5" fill="none" stroke="#fff" stroke-width="2.4"/><path d="M15 15l6 6" stroke="#fff" stroke-width="3" stroke-linecap="round"/></svg></div>
    <h3>Technology Research</h3>
    <p>Lorem ipsum dolor sit amet, consectetuer adipiscing elit. Lorem ipsum Lorem ipsum dolor</p>
    <span class="btn">READ MORE</span>
  </div>
  <div class="abs card" style="left:354px">
    <div class="icon"><svg width="50" height="50" viewBox="0 0 24 24"><rect x="3" y="4" width="18" height="13" fill="none" stroke="#fff" stroke-width="1.8"/><path d="M9 8l-3 2.5L9 13M15 8l3 2.5L15 13M8 21h8M12 17v4" fill="none" stroke="#fff" stroke-width="1.8"/></svg></div>
    <h3>Development</h3>
    <p>Lorem ipsum dolor sit amet, consectetuer adipiscing elit. Lorem ipsum Lorem ipsum dolor</p>
    <span class="btn">READ MORE</span>
  </div>
  <div class="abs card" style="left:609px">
    <div class="icon"><svg width="50" height="50" viewBox="0 0 24 24"><circle cx="12" cy="12" r="9" fill="none" stroke="#fff" stroke-width="1.8"/><path d="M3 12h18M12 3c3 3 3 15 0 18M12 3c-3 3-3 15 0 18" fill="none" stroke="#fff" stroke-width="1.4"/></svg></div>
    <h3>Travel Technology</h3>
    <p>Lorem ipsum dolor sit amet, consectetuer adipiscing elit. Lorem ipsum Lorem ipsum dolor</p>
    <span class="btn">READ MORE</span>
  </div>
  <div class="abs card" style="left:864px">
    <div class="icon"><svg width="50" height="50" viewBox="0 0 24 24"><circle cx="12" cy="12" r="4" fill="none" stroke="#fff" stroke-width="2"/><path d="M12 3v4M12 17v4M3 12h4M17 12h4M5.6 5.6l2.8 2.8M15.6 15.6l2.8 2.8M5.6 18.4l2.8-2.8M15.6 8.4l2.8-2.8" stroke="#fff" stroke-width="2"/></svg></div>
    <h3>Generation</h3>
    <p>Lorem ipsum dolor sit amet, consectetuer adipiscing elit. Lorem ipsum Lorem ipsum dolor</p>
    <span class="btn">READ MORE</span>
  </div>
</section>

<section>
  <div class="abs screen" role="img" aria-label="Desktop monitor showing a teal screen with a circular travel app illustration"></div>
  <div class="abs feature">
    <h2>TRAVEL TECHNOLOGY INDUSTRY</h2>
    <p>Nemo enim ipsam voluptatem quia voluptas sit aspernatur aut odit aut fugit, sed quia cour magni dolores eos qui ratione voluptatem sequi nesciunt. Neque porro squam est, qui rem ipsum quia dolor sit amet, consectetur, adipisci velit, sed quia non numquam eius modi tempora incidunt ut labore et dolore magnam aliquam quaerat voluptatem.</p>
    <p class="lead">Sed ut perspiciatis unde omnis iste natus error sit voluptatem accusantium doloremque laudantium, totam rem aperiam:</p>
    <ul>
      <li><svg width="12" height="10" viewBox="0 0 12 10"><path d="M1 5l3.5 3.5L11 1" fill="none" stroke="#3d3d3d" stroke-width="2"/></svg>Sed ut perspiciatis unde omnis iste natus</li>
      <li><svg width="12" height="10" viewBox="0 0 12 10"><path d="M1 5l3.5 3.5L11 1" fill="none" stroke="#3d3d3d" stroke-width="2"/></svg>Nemo enim ipsam voluptatem</li>
      <li><svg width="12" height="10" viewBox="0 0 12 10"><path d="M1 5l3.5 3.5L11 1" fill="none" stroke="#3d3d3d" stroke-width="2"/></svg>At vero eos et accusamus et iusto odio dignissimos ducimus</li>
    </ul>
  </div>
</section>

<section>
  <div class="abs blog"></div>
  <div class="abs sec-head blog-head">
    <svg width="184" height="10"><polygon points="0,5 184,0 184,10" fill="#6caf45"/></svg>
    <h2>LATEST BLOG</h2>
    <svg width="184" height="10"><polygon points="0,0 184,5 0,10" fill="#6caf45"/></svg>
  </div>
  <article class="abs post" style="left:99px">
    <div class="photo" role="img" aria-label="Tablet showing a travel booking screen" style="background:linear-gradient(135deg,#7a5a4a,#3f6f9a 60%,#2c3e55)"><div class="date">Feb<br>22, 2016</div></div>
    <h4>Phasellus at quam tristique, cursus</h4>
    <p>Etiam dignissim sit amet felis ac sagittis. Sed libero arcu, pharetra et ante in, elementum scelerisque arcu. Curabitur sagittis non justo at ultricies odio ac</p>
  </article>
  <article class="abs post" style="left:442px">
    <div class="photo" role="img" aria-label="Business travellers waiting in an airport lounge" style="background:linear-gradient(135deg,#c9c3bb,#8e8a86 55%,#5a5a5c)"><div class="date">Feb<br>22, 2016</div></div>
    <h4>Phasellus at quam tristique, cursus</h4>
    <p>Etiam dignissim sit amet felis ac sagittis. Sed libero arcu, pharetra et ante in, elementum scelerisque arcu. Curabitur sagittis non justo at ultricies odio ac</p>
  </article>
  <article class="abs post" style="left:784px">
    <div class="photo" role="img" aria-label="Businessman touching a glowing data display with a world map" style="background:linear-gradient(135deg,#1e3650,#3b6d94 50%,#1a2633)"><div class="date">Feb<br>22, 2016</div></div>
    <h4>Phasellus at quam tristique, cursus</h4>
    <p>Etiam dignissim sit amet felis ac sagittis. Sed libero arcu, pharetra et ante in, elementum scelerisque arcu. Curabitur sagittis non justo at ultricies odio ac</p>
  </article>
</section>

<footer>
  <div class="abs footer"></div>
  <div class="abs foot-brand">VOYAGE FORGE LABS</div>
  <div class="abs contact">
    <h4 class="foot-title">CONTACT US</h4>
    <div class="row"><svg width="14" height="18" viewBox="0 0 14 18"><path d="M7 1a6 6 0 0 0-6 6c0 4.5 6 10 6 10s6-5.5 6-10a6 6 0 0 0-6-6z" fill="none" stroke="#fff" stroke-width="1.5"/><circle cx="7" cy="7" r="2" fill="#fff"/></svg><span>Voyage Forge 118 Harbour Row<br>Lakeside , Oregon , 97000</span></div>
    <div class="row"><svg width="16" height="16" viewBox="0 0 24 24"><path d="M6.6 10.8a15 15 0 0 0 6.6 6.6l2.2-2.2c.3-.3.7-.4 1-.2 1.1.4 2.3.6 3.6.6.6 0 1 .4 1 1V20c0 .6-.4 1-1 1A17 17 0 0 1 3 4c0-.6.4-1 1-1h3.5c.6 0 1 .4 1 1 0 1.3.2 2.5.6 3.6.1.3 0 .7-.2 1z" fill="none" stroke="#fff" stroke-width="1.5"/></svg><span>Phone: 0400 555 019</span></div>
    <div class="row"><svg width="16" height="14" viewBox="0 0 24 18"><rect x="1" y="1" width="22" height="16" fill="none" stroke="#fff" stroke-width="1.8"/><path d="M1 1l11 9 11-9" fill="none" stroke="#fff" stroke-width="1.8"/></svg><span>E-mail: hello@voyageforge.example</span></div>
  </div>
  <div class="abs news">
    <h4 class="foot-title">JOIN OUR NEWSLETTER</h4>
    <p>Excepteur sint occaecat cupidatat non proident, sunt in culpa qui</p>
    <div class="field">Enter Name</div>
    <div class="actions"><span class="sub">SUBSCRIBE</span><i class="dot"></i><i class="dot"></i><i class="dot"></i><i class="dot"></i></div>
  </div>
  <div class="abs links">
    <h4 class="foot-title">QUICK LINKS</h4>
    <ul><li>Home</li><li>About Us</li><li>Services</li><li>Projects</li><li>News</li><li>Contact Us</li></ul>
  </div>
  <div class="abs bottom">Copyright 2016 | All Rights Reserved – Voyage Forge Labs</div>
</footer>

</body>
</html>
```